1 Banner für Affiliate-Marketing (Börse/Trading)
Zielgruppe
Wir vermitteln Kunden an einen Broker. Die Kunden eröffnen Handelskonten, in denen sie selbständig Finanzprodukte (CFDs, Forex, Aktien, Edelmetalle,...) gehebelt handeln. Wir bieten dem Kunden eine Dienstleistung an, indem wir Broker vorauswählen, technischen Support liefern, bei der Kontoeröffnung unterstützen und auf Wunsch auch Trader ausbilden.
Zielgruppe: männlich, finanz- und risikoaffin, Spekulant
Aufgabenstellung
Wir benötigen 1 klickstarken Banner für das Affiliate-Marketing
Bannergröße: 300*250
Formate: GIF, PNG, JPG, Vektor
Gerne auch animierte Vorschläge, aber bitte nicht ausschließlich.
Zusätzliche Info, die verarbeitet werden kann (aber nicht muss): Kelvora Bank hat in 2016 bei 2 Kundenumfragen den Testsieg als bester Broker gewonnen.
Design ist frei und muss sich nicht an der Homepage orientieren - vielmehr suchen wir klickstarke Banner aus der Finanz-/Börsenwelt mit Bildern Ihrer Wahl.

```html
<!DOCTYPE html>
<html lang="de">
<head>
<meta charset="utf-8">
<title>Kelvora Bank – Bannerset Testsieger 2016</title>
<link rel="stylesheet" href="https://fonts.googleapis.com/css2?family=Ubuntu:wght@400;500;700&family=Open+Sans:wght@700&display=swap">
<style>
  :root {
    --stage: #232323;
    --blue-light: #2a63c4;
    --blue: #1a4aa3;
    --blue-deep: #0b2a6e;
    --navy: #06163f;
    --yellow: #ffdc00;
    --yellow-dark: #e6b800;
    --ink: #0a1636;
    --orange: #e8501c;
    --white: #ffffff;
    --label: #f2f2f2;
  }
  * { box-sizing: border-box; margin: 0; padding: 0; }
  html, body { width: 1200px; height: 857px; overflow: hidden; background: var(--stage); }
  body { position: relative; font-family: "Ubuntu", sans-serif; }

  .size-label {
    position: absolute;
    font-family: "Open Sans", sans-serif;
    font-weight: 700;
    font-size: 14px;
    color: var(--label);
    letter-spacing: 0.5px;
  }

  .banner {
    position: absolute;
    overflow: hidden;
    background: linear-gradient(160deg, var(--blue-light) 0%, var(--blue) 45%, var(--blue-deep) 100%);
  }
  .banner > * { position: absolute; }

  .scene { background: radial-gradient(ellipse at 70% 40%, rgba(10,35,95,0.85) 0%, rgba(6,22,63,0.6) 45%, rgba(6,22,63,0) 75%); }
  .scene--screen { background: linear-gradient(170deg, #0b1a3c 0%, #050d22 60%, #0d2c66 100%); }

  .logo-band { background: var(--yellow); }
  .logo-name {
    font-weight: 700;
    color: var(--ink);
    text-transform: uppercase;
    line-height: 0.92;
    letter-spacing: 0.2px;
  }

  .kicker { font-weight: 700; color: var(--white); white-space: nowrap; }
  .headline { font-weight: 700; color: var(--white); text-transform: uppercase; line-height: 0.92; white-space: nowrap; }
  .year {
    background: var(--yellow);
    color: var(--ink);
    font-weight: 700;
    display: flex; align-items: center; justify-content: center;
    line-height: 1;
  }

  .badge {
    border-radius: 50%;
    background: var(--orange);
    border: 2px solid var(--white);
    box-shadow: 0 0 0 2px rgba(10,22,54,0.55), 0 3px 8px rgba(0,0,0,0.45);
    display: flex; align-items: center; justify-content: center;
    color: var(--white);
    text-align: center;
  }
  .badge span { display: block; transform: rotate(-12deg); line-height: 1.08; font-weight: 400; text-transform: uppercase; }

  .cta {
    background: linear-gradient(180deg, #ffe94d 0%, var(--yellow) 45%, var(--yellow-dark) 100%);
    border-radius: 4px;
    color: var(--ink);
    font-weight: 700;
    display: flex; align-items: center; justify-content: space-between;
    box-shadow: 0 2px 4px rgba(0,0,0,0.4);
    white-space: nowrap;
  }
  .cta svg { flex: none; }
</style>
</head>
<body>

<!-- 728 x 90 -->
<div class="size-label" style="left:58px; top:88px;">728 X 90</div>
<div class="banner" style="left:57px; top:122px; width:624px; height:77px;">
  <div class="scene" role="img" aria-label="Geschäftsmann in Silhouette vor einem Tablet mit Börsenkursen" style="left:420px; top:0; width:204px; height:77px;"></div>
  <div class="logo-band" style="left:0; top:0; width:131px; height:77px; clip-path:polygon(0 0,100% 0,88% 100%,0 100%);"></div>
  <div class="logo-name" style="left:7px; top:17px; font-size:21px;">Kelvora<br>Bank</div>
  <div class="kicker" style="left:186px; top:4px; font-size:17px;">Testsieger</div>
  <div class="headline" style="left:143px; top:27px; font-size:20px;">Bester<br>Broker</div>
  <div class="year" style="left:234px; top:29px; width:91px; height:33px; font-size:28px;">2016</div>
  <div class="badge" style="left:371px; top:-1px; width:80px; height:80px;"><span style="font-size:10px;">Günstiger<br>im GER30<br>ist keiner!</span></div>
  <div class="cta" style="left:500px; top:45px; width:116px; height:23px; padding:0 3px 0 7px; font-size:11px;">HIER KLICKEN
    <svg width="17" height="17" viewBox="0 0 20 20"><circle cx="10" cy="10" r="9" fill="#d9a800"/><path d="M8 5l5 5-5 5" fill="none" stroke="#fff" stroke-width="2.4" stroke-linecap="round" stroke-linejoin="round"/></svg>
  </div>
</div>

<!-- 468 x 60 -->
<div class="size-label" style="left:704px; top:88px;">468 X 60</div>
<div class="banner" style="left:702px; top:122px; width:401px; height:51px;">
  <div class="logo-band" style="left:0; top:0; width:80px; height:51px; clip-path:polygon(0 0,100% 0,88% 100%,0 100%);"></div>
  <div class="logo-name" style="left:5px; top:10px; font-size:13px;">Kelvora<br>Bank</div>
  <div class="kicker" style="left:127px; top:1px; font-size:12px;">Testsieger</div>
  <div class="headline" style="left:94px; top:17px; font-size:15px;">Bester<br>Broker</div>
  <div class="year" style="left:164px; top:20px; width:71px; height:24px; font-size:21px;">2016</div>
  <div class="badge" style="left:240px; top:-12px; width:76px; height:76px;"><span style="font-size:10px;">Günstiger<br>im GER30<br>ist keiner!</span></div>
  <div class="cta" style="left:323px; top:15px; width:75px; height:19px; padding:0 5px; font-size:8.5px; justify-content:center;">HIER KLICKEN</div>
</div>

<!-- 120 x 600 -->
<div class="banner" style="left:57px; top:243px; width:104px; height:514px;">
  <div class="scene" role="img" aria-label="Geschäftsmann in Silhouette" style="left:0; top:230px; width:104px; height:170px;"></div>
  <div class="scene scene--screen" role="img" aria-label="Tablet mit Börsenchart" style="left:0; top:400px; width:104px; height:114px;"></div>
  <div class="logo-band" style="left:0; top:0; width:104px; height:63px; clip-path:polygon(0 0,100% 0,100% 90%,0 100%);"></div>
  <div class="logo-name" style="left:4px; top:9px; font-size:19px;">Kelvora<br>Bank</div>
  <div class="kicker" style="left:8px; top:112px; font-size:15px;">Testsieger</div>
  <div class="headline" style="left:5px; top:140px; font-size:23px;">Bester<br>Broker</div>
  <div class="year" style="left:5px; top:185px; width:94px; height:34px; font-size:28px;">2016</div>
  <div class="badge" style="left:6px; top:335px; width:90px; height:90px;"><span style="font-size:11.5px;">Günstiger<br>im GER30<br>ist keiner!</span></div>
  <div class="cta" style="left:3px; top:486px; width:96px; height:20px; padding:0 2px 0 6px; font-size:9px;">HIER KLICKEN
    <svg width="14" height="14" viewBox="0 0 20 20"><circle cx="10" cy="10" r="9" fill="#d9a800"/><path d="M8 5l5 5-5 5" fill="none" stroke="#fff" stroke-width="2.4" stroke-linecap="round" stroke-linejoin="round"/></svg>
  </div>
</div>
<div class="size-label" style="left:57px; top:767px;">120 X 600</div>

<!-- 160 x 600 -->
<div class="banner" style="left:200px; top:243px; width:137px; height:514px;">
  <div class="scene" role="img" aria-label="Geschäftsmann in Silhouette" style="left:0; top:270px; width:137px; height:150px;"></div>
  <div class="scene scene--screen" role="img" aria-label="Tablet mit Börsenchart" style="left:0; top:400px; width:137px; height:114px;"></div>
  <div class="logo-band" style="left:0; top:0; width:137px; height:63px; clip-path:polygon(0 0,100% 0,100% 90%,0 100%);"></div>
  <div class="logo-name" style="left:10px; top:8px; font-size:24px;">Kelvora<br>Bank</div>
  <div class="kicker" style="left:17px; top:114px; font-size:17px;">Testsieger</div>
  <div class="headline" style="left:7px; top:140px; font-size:31px;">Bester<br>Broker</div>
  <div class="year" style="left:7px; top:200px; width:124px; height:46px; font-size:35px;">2016</div>
  <div class="badge" style="left:8px; top:327px; width:106px; height:106px;"><span style="font-size:14px;">Günstiger<br>im GER30<br>ist keiner!</span></div>
  <div class="cta" style="left:4px; top:476px; width:128px; height:26px; padding:0 3px 0 9px; font-size:12px;">HIER KLICKEN
    <svg width="19" height="19" viewBox="0 0 20 20"><circle cx="10" cy="10" r="9" fill="#d9a800"/><path d="M8 5l5 5-5 5" fill="none" stroke="#fff" stroke-width="2.4" stroke-linecap="round" stroke-linejoin="round"/></svg>
  </div>
</div>
<div class="size-label" style="left:203px; top:767px;">160 X 600</div>

<!-- 500 x 500 -->
<div class="banner" style="left:377px; top:243px; width:429px; height:429px;">
  <div class="scene" role="img" aria-label="Geschäftsmann in Anzug von hinten, Silhouette vor Kursanzeige" style="left:190px; top:170px; width:239px; height:259px;"></div>
  <div class="scene scene--screen" role="img" aria-label="Tablet mit Börsenkursen und Chart" style="left:0; top:285px; width:160px; height:144px; clip-path:polygon(0 0,100% 22%,90% 100%,0 100%);"></div>
  <div class="logo-band" style="left:0; top:0; width:429px; height:58px; clip-path:polygon(0 0,100% 0,100% 85%,50% 100%,0 92%);"></div>
  <div class="logo-name" style="left:0; top:6px; width:429px; text-align:center; font-size:43px;">Kelvora Bank</div>
  <div class="kicker" style="left:0; top:70px; width:429px; text-align:center; font-size:38px;">Testsieger</div>
  <div class="headline" style="left:20px; top:120px; font-size:49px;">Bester<br>Broker</div>
  <div class="year" style="left:214px; top:125px; width:201px; height:74px; font-size:64px;">2016</div>
  <div class="badge" style="left:86px; top:235px; width:120px; height:120px;"><span style="font-size:16px;">Günstiger<br>im GER30<br>ist keiner!</span></div>
  <div class="cta" style="left:191px; top:364px; width:225px; height:47px; padding:0 5px 0 16px; font-size:24px;">HIER KLICKEN
    <svg width="36" height="36" viewBox="0 0 20 20"><circle cx="10" cy="10" r="9" fill="#d9a800"/><path d="M8 5l5 5-5 5" fill="none" stroke="#fff" stroke-width="2.4" stroke-linecap="round" stroke-linejoin="round"/></svg>
  </div>
</div>
<div class="size-label" style="left:379px; top:693px;">500 X 500</div>

<!-- 300 x 250 -->
<div class="banner" style="left:845px; top:243px; width:258px; height:214px;">
  <div class="scene" role="img" aria-label="Geschäftsmann in Silhouette" style="left:150px; top:100px; width:108px; height:114px;"></div>
  <div class="scene scene--screen" role="img" aria-label="Tablet mit Börsenchart" style="left:0; top:150px; width:80px; height:64px;"></div>
  <div class="logo-band" style="left:0; top:0; width:258px; height:37px; clip-path:polygon(0 0,100% 0,100% 85%,50% 100%,0 92%);"></div>
  <div class="logo-name" style="left:0; top:4px; width:258px; text-align:center; font-size:26px;">Kelvora Bank</div>
  <div class="kicker" style="left:0; top:45px; width:244px; text-align:center; font-size:20px;">Testsieger</div>
  <div class="headline" style="left:18px; top:73px; font-size:26px;">Bester<br>Broker</div>
  <div class="year" style="left:127px; top:76px; width:111px; height:42px; font-size:33px;">2016</div>
  <div class="badge" style="left:30px; top:125px; width:80px; height:80px;"><span style="font-size:10.5px;">Günstiger<br>im GER30<br>ist keiner!</span></div>
  <div class="cta" style="left:132px; top:183px; width:117px; height:23px; padding:0 3px 0 8px; font-size:11.5px;">HIER KLICKEN
    <svg width="17" height="17" viewBox="0 0 20 20"><circle cx="10" cy="10" r="9" fill="#d9a800"/><path d="M8 5l5 5-5 5" fill="none" stroke="#fff" stroke-width="2.4" stroke-linecap="round" stroke-linejoin="round"/></svg>
  </div>
</div>
<div class="size-label" style="left:845px; top:472px;">300 X 250</div>

</body>
</html>
```